We need professional looking business cards for our e-assessment business based in Europe. Our company is called Velmo.

You can just use sample name and addresses.

The colours we use are:

#70abe4 (blue)
#FF6600 (orange)

The back side should say: Online testing made clear

This is the print-shop we are using. Please look at the link for info about formats: http://nl.prindavo.com/help/faq/using-my-own-artwork.html

Target market is education and large corporations

Business

```html
<!DOCTYPE html>
<html lang="en">
<head>
<meta charset="utf-8">
<title>Velmo business cards</title>
<link rel="stylesheet" href="https://fonts.googleapis.com/css2?family=Questrial&display=swap">
<style>
  :root {
    --velmo-orange: #ff6600;
    --velmo-blue: #70abe4;
    --card-dark: #2c2c2e;
    --card-light: #ffffff;
    --card-light-shade: #e9e9e9;
    --ink: #3a3a3a;
    --ink-soft: #555555;
    --backdrop: #d9d6d1;
  }
  * { box-sizing: border-box; margin: 0; padding: 0; }
  html, body {
    width: 1200px;
    height: 871px;
    overflow: hidden;
    background: var(--backdrop);
    font-family: "Questrial", sans-serif;
  }
  .canvas {
    position: relative;
    width: 1200px;
    height: 871px;
  }
  .card {
    position: absolute;
    width: 580px;
    height: 362px;
    border-radius: 3px;
    box-shadow: 0 14px 30px rgba(0, 0, 0, 0.28);
    overflow: hidden;
  }
  /* Back side */
  .card-back {
    left: 70px;
    top: 90px;
    background: var(--card-dark);
  }
  .card-back .brand-disc {
    position: absolute;
    left: 50%;
    top: 72px;
    width: 156px;
    height: 156px;
    margin-left: -78px;
    border-radius: 50%;
    background: var(--velmo-orange);
  }
  .card-back .tagline {
    position: absolute;
    left: 0;
    right: 0;
    top: 270px;
    text-align: center;
    color: var(--velmo-blue);
    font-size: 19px;
    letter-spacing: 0.12em;
  }
  /* Front side */
  .card-front {
    left: 550px;
    top: 420px;
    background: linear-gradient(160deg, var(--card-light) 35%, var(--card-light-shade) 100%);
  }
  .wordmark {
    position: absolute;
    left: 34px;
    top: 190px;
    display: flex;
    align-items: center;
    gap: 18px;
  }
  .wordmark .brand-dot {
    width: 66px;
    height: 66px;
    border-radius: 50%;
    background: var(--velmo-orange);
  }
  .wordmark .brand-name {
    color: var(--ink);
    font-size: 64px;
    line-height: 1;
  }
  .contact {
    position: absolute;
    left: 345px;
    top: 224px;
    width: 220px;
    color: var(--ink-soft);
    font-size: 14px;
    font-style: normal;
    line-height: 1.55;
    letter-spacing: 0.04em;
  }
  .contact .person {
    color: var(--ink);
    font-size: 18px;
    letter-spacing: 0.1em;
    margin-bottom: 6px;
  }
  .contact .company {
    color: var(--velmo-orange);
  }
</style>
</head>
<body>
  <main class="canvas">
    <section class="card card-back" aria-label="Card back">
      <div class="brand-disc"></div>
      <p class="tagline">Online testing made clear</p>
    </section>

    <section class="card card-front" aria-label="Card front">
      <div class="wordmark">
        <span class="brand-dot"></span>
        <span class="brand-name">velmo</span>
      </div>
      <address class="contact">
        <p class="person">Jorin F Sallen</p>
        <p class="company">velmo inc</p>
        <p>25 Tessa Street, Varnhollow</p>
        <p>QLD 4172</p>
      </address>
    </section>
  </main>
</body>
</html>
```